Design 2 8x10 one page sales brochures for KELTRIM, a cloud service provider.

We’re open to fun and creative, yet must be clean, bold and professional.

***The winning designer will also be hired to design a handful of other brochures for us after the contest***

We understand the value of feedback and will work closely with every design to create the perfect sales brochure!

Should be printer friendly, primarily white so doesn’t consume a lot of printer ink
Colors - grey, black, light blue, llight green
We are a fun, easy to work with technology company and the brochures need to reflect taht.

Don't hesitate to ask any questions, thanks!

We need two designs, each one page 8x10"
#1 Why we're Kel
#2 KELTalk

Target Market(s)

Small and medium sized business owners

Industry/Entity Type

Telecommunications

Font styles to use
Sans Serif

Requirements
Must have
• Clean, professional designs. We're a fun tech company.
• Visually appealing
Nice to have
• graphs, charts, diagrams, etc
Should not have
• not sure.

```html
<!DOCTYPE html>
<html lang="en">
<head>
<meta charset="utf-8">
<title>KELTRIM – Cloud Made Easy</title>
<link rel="stylesheet" href="https://fonts.googleapis.com/css2?family=Amaranth:wght@700&family=Fira+Sans:wght@500;600&family=Open+Sans:wght@400;600;700&display=swap">
<style>
  :root {
    --page-bg: #e9e9ea;
    --ink-dark: #232427;
    --ink-soft: #44474d;
    --sky: #1ba1de;
    --aqua: #21c7dc;
    --teal-head: #1a8fc0;
    --text-body: #6a6d72;
    --text-dark: #222;
    --grey-brand: #8b8d91;
    --white: #ffffff;
  }
  * { margin: 0; padding: 0; box-sizing: border-box; }
  html, body { width: 1200px; height: 1200px; overflow: hidden; background: var(--page-bg); }
  .brochure {
    position: absolute; left: 120px; top: 0; width: 960px; height: 1200px;
    overflow: hidden; background: var(--ink-dark);
    font-family: "Open Sans", sans-serif;
  }
  .brochure-shapes { position: absolute; inset: 0; }
  .abs { position: absolute; }

  .brand-top { left: 474px; top: 40px; display: flex; align-items: center; gap: 20px; }
  .brand-dot { width: 120px; height: 120px; border-radius: 50%; border: 12px solid var(--sky); }
  .brand-name { font: 700 58px/1 "Open Sans", sans-serif; color: var(--sky); letter-spacing: 1px; }
  .brand-tagline { font: 600 24px/1 "Open Sans", sans-serif; color: var(--white); letter-spacing: 1px; margin-top: 8px; }

  .headline {
    left: 0; top: 196px; width: 540px; text-align: center; white-space: nowrap;
    font-family: "Amaranth", sans-serif; font-weight: 700; color: var(--sky);
    text-shadow: 0 2px 6px rgba(0,0,0,.8);
  }
  .headline span { display: block; }
  .headline .l1 { font-size: 42px; line-height: 46px; }
  .headline .l2 { font-size: 38px; line-height: 48px; }
  .headline .l3 { font-size: 38px; line-height: 54px; }
  .headline .accent { color: var(--aqua); font-size: 48px; display: inline; }

  .hero-mark { left: 517px; top: 352px; width: 200px; text-align: center; }
  .hero-mark .brand-dot { width: 90px; height: 90px; border-width: 10px; margin: 0 auto 14px; }
  .hero-mark .brand-name { font-size: 36px; color: var(--ink-soft); }

  .tick { width: 52px; height: 52px; }
  .feature-title { font: 700 14px/1 "Open Sans", sans-serif; color: var(--text-dark); text-align: center; }
  .feature-body { font-size: 11px; color: var(--text-body); text-align: justify; }
  .feature-left .feature-body { line-height: 22.5px; }
  .feature-right .feature-body { line-height: 29.6px; }
  .divider { left: 464px; top: 622px; width: 2px; height: 257px; background: #c8c9cb; }

  .standard { left: 250px; top: 928px; width: 630px; text-align: center; }
  .standard h2 { font: 600 21px/45px "Fira Sans", sans-serif; color: var(--teal-head); }
  .products { margin-top: 2px; font-size: 14px; color: var(--text-dark); }
  .products i { display: inline-block; width: 6px; height: 6px; border-radius: 50%; background: var(--sky); margin: 0 9px 2px; vertical-align: middle; }

  .brand-bottom { left: 380px; top: 1072px; display: flex; align-items: center; gap: 16px; }
  .brand-bottom .brand-dot { width: 74px; height: 74px; border-width: 9px; }
  .brand-bottom .brand-name { font-size: 42px; }
  .brand-bottom .brand-tagline { font-size: 16px; color: var(--grey-brand); margin-top: 4px; font-weight: 400; }

  .contact {
    left: 245px; top: 1172px; width: 597px; height: 28px;
    display: flex; align-items: center; justify-content: center; gap: 10px;
    font: 700 17px/1 "Open Sans", sans-serif; color: var(--white);
  }
  .contact svg { width: 13px; height: 13px; }
</style>
</head>
<body>
<main class="brochure">
  <svg class="brochure-shapes" width="960" height="1200" viewBox="0 0 960 1200" aria-hidden="true">
    <defs>
      <linearGradient id="aquaFade" x1="0" y1="0" x2="1" y2="1">
        <stop offset="0" stop-color="#1ba1de"/><stop offset="1" stop-color="#27d3d6"/>
      </linearGradient>
    </defs>
    <polygon points="477,0 960,0 960,509 360,105" fill="#2c2e33"/>
    <polygon points="212,0 477,0 349,90" fill="url(#aquaFade)"/>
    <polygon points="0,685 614,275 960,509 960,1200 0,1200" fill="#ffffff"/>
    <polygon points="0,964 50,928 245,1098 245,1200 0,1200" fill="#2b2d31"/>
    <polygon points="143,1003 245,916 245,1098" fill="#45484e"/>
    <rect x="0" y="1098" width="245" height="102" fill="#1d1e21"/>
    <polygon points="911,936 911,1068 842,999" fill="url(#aquaFade)"/>
    <polygon points="842,999 955,1098 842,1200" fill="#26282c"/>
    <polygon points="911,1146 960,1200 842,1200" fill="url(#aquaFade)"/>
    <rect x="245" y="1172" width="597" height="28" fill="#232427"/>
  </svg>

  <div class="abs brand-top">
    <div class="brand-dot"></div>
    <div>
      <div class="brand-name">KELTRIM</div>
      <div class="brand-tagline">cloud made easy</div>
    </div>
  </div>

  <h1 class="abs headline">
    <span class="l1">Your</span>
    <span class="l2">Business Communications</span>
    <span class="l3">don’t have to be <span class="accent">lame</span></span>
  </h1>

  <div class="abs hero-mark">
    <div class="brand-dot"></div>
    <div class="brand-name">KELTRIM</div>
  </div>

  <section class="feature-left">
    <svg class="abs tick" style="left:214px;top:581px" viewBox="0 0 52 52" aria-hidden="true">
      <circle cx="26" cy="26" r="23" fill="none" stroke="#1ba1de" stroke-width="4"/>
      <circle cx="26" cy="26" r="15" fill="#1ba1de"/>
      <polyline points="19,26 24,31 33,21" fill="none" stroke="#fff" stroke-width="4" stroke-linecap="round" stroke-linejoin="round"/>
    </svg>
    <h3 class="abs feature-title" style="left:55px;top:658px;width:372px">Cloud Made Easy</h3>
    <p class="abs feature-body" style="left:55px;top:680px;width:372px">Keltrim delivers customized cloud solutions to enterprises and small businesses with the highest level of value, integrity, service, and support -radically changing your ability to communicate and compete in the market 100+ years of collective experience activating over 1M user seats, working with some of the largest organizations in the world. We leveraged our experiences to build an innovative suite of cloud offerings and features, allowing us to build custom solutions based on unique and changing customer needs.</p>
  </section>

  <div class="abs divider"></div>

  <section class="feature-right">
    <svg class="abs tick" style="left:679px;top:581px" viewBox="0 0 52 52" aria-hidden="true">
      <circle cx="26" cy="26" r="23" fill="none" stroke="#1ba1de" stroke-width="4"/>
      <circle cx="26" cy="26" r="15" fill="#1ba1de"/>
      <polyline points="19,26 24,31 33,21" fill="none" stroke="#fff" stroke-width="4" stroke-linecap="round" stroke-linejoin="round"/>
    </svg>
    <h3 class="abs feature-title" style="left:505px;top:662px;width:400px">Storm-Ready Triple Backup Network (STBN):</h3>
    <p class="abs feature-body" style="left:505px;top:684px;width:400px">The only way our network is going down if if a meteor shower simultaneously wipes out our 3 geographical redundant data centers. The statistical likelihood of that happening is virtually non-existent. Make your business’s communications not lame system phone system not lame with KELTalk: an easy, worry-free way to communicate!</p>
  </section>

  <section class="abs standard">
    <h2>KELTRIM’s radical cloud solutions are setting the new standard<br>for enterprise grade cloud:</h2>
    <p class="products">KELTalk<i></i>KELCallCenter<i></i>KELMeetings<i></i>KELApps (mobile, desktop, web)</p>
  </section>

  <div class="abs brand-bottom">
    <div class="brand-dot"></div>
    <div>
      <div class="brand-name">KELTRIM</div>
      <div class="brand-tagline">cloud made easy</div>
    </div>
  </div>

  <footer class="abs contact">
    <svg viewBox="0 0 14 14" aria-hidden="true"><circle cx="7" cy="7" r="6.5" fill="#bbb"/><rect x="3.5" y="4.5" width="7" height="5" fill="none" stroke="#232427" stroke-width="1"/></svg>
    <span>sales@keltrim.com</span>
    <svg viewBox="0 0 14 14" aria-hidden="true"><circle cx="7" cy="7" r="6" fill="none" stroke="#bbb" stroke-width="1.5"/><line x1="1" y1="7" x2="13" y2="7" stroke="#bbb"/><ellipse cx="7" cy="7" rx="2.5" ry="6" fill="none" stroke="#bbb"/></svg>
    <span>www.keltrim.com</span>
    <svg viewBox="0 0 14 14" aria-hidden="true"><circle cx="7" cy="7" r="6.5" fill="#bbb"/><path d="M4 5h6l-1 4H5z" fill="#232427"/></svg>
    <span>555-014-2276</span>
  </footer>
</main>
</body>
</html>
```